Valdane Companies Business Card Design

We need a new business card for our Private Equity Real Estate Development firm, “Valdane” and our EB-5 regional center “Thornmere Regional Center” on one card. We prefer a design that is simple, elegant, and represents the luxury products we design and build as well as the financial security and stability our successful history has produced. We are an industry leader in our field and 3rd generation family business that has evolved into an institutional quality investment platform. Considered design size is standard business card dimensions (3.5 x 2 inches with an additional 1/8 inch space for design elements or backgrounds that extend beyond the finished size of your piece.

Target Market(s)

• High net worth individuals
• Highly skilled technical workers and physicians in the US seeking investment-based immigration opportunities
• Sophisticated private equity investors
• Intermediary partners include domestic attorneys and investment brokers, as well as international agent networks
• US real estate developers

Industry/Entity Type

Finance

Contact Information for Business Card

(Providing placeholder info for personal information, please design for longer character spaces, longer names and addresses etc..)
• Logo for Valdane
• Logo for Thornmere Regional Center
• Full name: Marcus Valdane
• Job title: CEO
• Email address: mvaldane@valdanecompanies.com
• Cell phone number: +1.555.314.2287
• Office number +1.555.628.4410
• Office address: Larkfield Court 5, 4817 Vista Orilla, San Ramon, CA.
• Website: www.valdanecompanies.com

Font styles to use
Serif
Sans Serif

Colors
ec1f27
ffffff
000000

Requirements
Must have
• • Logo for Valdane
• • Logo for Thornmere Regional Center
• - Use rounded corners
• (See .ai file included for logos)
Nice to have
• • Simple, elegant design
• • Aesthetically compatible with our website design (www.valdanecompanies.com)
• • Color palette including but not limited to white, black, and red (as per logos)
Should not have
• - Not too much red color
• - Do not stack both logos on top of each other

```html
<!DOCTYPE html>
<html lang="en">
<head>
<meta charset="utf-8">
<title>Valdane Companies Business Card</title>
<link rel="stylesheet" href="https://fonts.googleapis.com/css2?family=Cinzel:wght@400;600;700&family=Source+Sans+3:wght@400;600&display=swap">
<style>
  :root {
    --backdrop: #7d7d7d;
    --card-light: #eeeeee;
    --card-dark: #333333;
    --card-dark-edge: #3a3a3a;
    --ink: #1e1e1e;
    --ink-soft: #2b2b2b;
    --rule: #c4c4c4;
    --silver: #c9c9c9;
    --silver-soft: #a9a9a9;
  }
  * { margin: 0; padding: 0; box-sizing: border-box; }
  html, body { width: 1200px; height: 1200px; overflow: hidden; }
  body {
    position: relative;
    background: var(--backdrop);
    font-family: "Source Sans 3", "Helvetica Neue", Arial, sans-serif;
    color: var(--ink);
  }
  .card {
    position: absolute;
    top: 311px;
    width: 366px;
    height: 593px;
    border-radius: 4px;
    box-shadow: 0 2px 4px rgba(0,0,0,0.35);
  }
  .card--front { left: 233px; background: var(--card-light); text-align: center; }
  .card--back {
    left: 628px;
    width: 369px;
    background: linear-gradient(160deg, var(--card-dark-edge) 0%, var(--card-dark) 55%, #2e2e2e 100%);
    text-align: center;
  }

  .brand { position: absolute; left: 0; right: 0; }
  .brand__mark { display: block; margin: 0 auto; }
  .card--front .brand { top: 92px; }
  .card--front .brand__mark { width: 44px; height: 44px; background: var(--ink-soft); margin-bottom: 44px; }
  .card--front .brand__name {
    font-family: "Cinzel", Georgia, serif;
    font-weight: 700;
    font-size: 36px;
    line-height: 1.1;
    color: var(--ink-soft);
    letter-spacing: 0.5px;
  }

  .person { position: absolute; left: 0; right: 0; top: 336px; }
  .person__name {
    font-family: "Cinzel", Georgia, serif;
    font-weight: 600;
    font-size: 21px;
    letter-spacing: 0.5px;
  }
  .person__title { font-size: 15px; margin-top: 2px; }
  .rule { width: 227px; height: 1px; background: var(--rule); margin: 0 auto; }
  .person .rule { margin-top: 12px; }

  .contact { list-style: none; margin: 9px 0 10px; font-size: 15.5px; line-height: 21.5px; }
  .contact__label { font-weight: 600; margin-right: 4px; }

  .address { font-size: 15.5px; line-height: 21px; margin-top: 9px; }

  .card--back .brand { top: 326px; }
  .card--back .brand__mark { width: 60px; height: 60px; background: var(--silver-soft); margin-bottom: 40px; }
  .card--back .brand__name {
    font-family: "Cinzel", Georgia, serif;
    font-weight: 600;
    font-size: 30px;
    line-height: 1.25;
    color: var(--silver);
    letter-spacing: 1px;
    padding: 0 30px;
  }
</style>
</head>
<body>
  <section class="card card--front" aria-label="Card front">
    <div class="brand">
      <span class="brand__mark"></span>
      <div class="brand__name">Valdane Capital</div>
    </div>
    <div class="person">
      <div class="person__name">MARCUS VALDANE</div>
      <div class="person__title">CEO</div>
      <div class="rule"></div>
      <ul class="contact">
        <li><span class="contact__label">P:</span>+1.555.314.2287</li>
        <li><span class="contact__label">M:</span>+1.555.628.4410</li>
        <li><span class="contact__label">E:</span>mvaldane@valdanecompanies.com</li>
        <li><span class="contact__label">W:</span>www.valdanecompanies.com</li>
      </ul>
      <div class="rule"></div>
      <p class="address">Larkfield Court 5, 4817 Vista<br>Orilla, San Ramon, CA</p>
    </div>
  </section>

  <section class="card card--back" aria-label="Card back">
    <div class="brand">
      <span class="brand__mark"></span>
      <div class="brand__name">Thornmere Regional Center</div>
    </div>
  </section>
</body>
</html>
```